We are a local Communty Pharmacy wishing to promote and market a specialised Pharmaceutical Service

We would like a design that is professional and enticing ( according to the brief In attached files)
We wish to Market Compounding Pharmacy as a specialist side of our business.
We have the expertise a purpose built preparation laboratory.
The main purpose is an Internet presence that entices prospective patients to contact or visit our physical store.

Target Market(s)

Patients Medicos and Veterinary clients

Industry/Entity Type

Pharmacy

Coding

Coded - Design and coding required

Number of Pages Required

1 page

Requirements
Must have
• Clear friendly image
Nice to have
• soft enticing feel
Should not have
• No crass loud unprofessional elements

```html
<!DOCTYPE html>
<html lang="en">
<head>
<meta charset="utf-8">
<title>Meadowbank Pharmacy – Compounding</title>
<link rel="stylesheet" href="https://fonts.googleapis.com/css2?family=Open+Sans:wght@400;600;700&display=swap">
<style>
:root{
  --blue:#2e8fd6;
  --blue-dark:#1f78bb;
  --green:#7dbf42;
  --orange:#f2892a;
  --ink:#3a3a3a;
  --muted:#6b6b6b;
  --line:#e3e3e3;
  --hero-a:#eef3f6;
  --hero-b:#c9d6de;
  --map:#e9ecee;
}
*{box-sizing:border-box;margin:0;padding:0}
html,body{width:1200px;height:2200px;overflow:hidden}
body{font-family:"Open Sans",Arial,sans-serif;color:var(--ink);background:#fff;display:flex;flex-direction:column}
.topbar{flex:none;height:24px;background:var(--blue);color:#fff;font-size:11px;display:flex;align-items:center;gap:22px;padding-left:96px}
.header{flex:none;height:66px;display:flex;align-items:center;justify-content:space-between;padding:0 95px}
.brand{display:flex;align-items:center;gap:10px;font-weight:700;font-size:17px;color:var(--blue);letter-spacing:.5px;text-transform:uppercase}
.brand-dot{width:28px;height:28px;border-radius:50%;background:var(--green)}
.nav{display:flex;gap:4px;font-size:11px;font-weight:600;text-transform:uppercase}
.nav a{color:var(--ink);text-decoration:none;padding:9px 14px}
.nav a.active{background:var(--blue);color:#fff}
.hero{flex:none;position:relative;height:530px;background:linear-gradient(135deg,var(--hero-a) 0%,#f7f9fa 40%,var(--hero-b) 100%)}
.hero-photo{position:absolute;inset:0}
.hero-copy{position:absolute;top:198px;left:0;right:0;text-align:center}
.hero-title{font-size:40px;font-weight:400;font-variant:small-caps;letter-spacing:1px;color:#2b2b2b}
.hero-text{margin:10px auto 0;width:680px;font-size:13px;color:var(--blue-dark)}
.btn{display:inline-block;margin-top:16px;border:1px solid var(--blue);color:var(--blue);font-size:11px;padding:6px 18px;background:rgba(255,255,255,.7)}
.arrow{position:absolute;top:245px;width:34px;height:34px;border-radius:50%;background:rgba(255,255,255,.8);display:flex;align-items:center;justify-content:center}
.arrow.left{left:14px}.arrow.right{right:14px}
.features{flex:none;display:flex;gap:55px;justify-content:center;margin-top:80px}
.feature{width:300px;height:190px;color:#fff;text-align:center;padding-top:26px}
.feature.green{background:var(--green)}.feature.blue{background:var(--blue)}.feature.orange{background:var(--orange)}
.feature h3{font-size:20px;font-weight:400;font-variant:small-caps;margin:12px 0 8px;letter-spacing:.5px}
.feature p{font-size:12px;line-height:1.5;width:230px;margin:0 auto}
.section-title{text-align:center;font-size:30px;font-weight:400;font-variant:small-caps;letter-spacing:1px}
.section-title::after{content:"";display:block;width:70px;height:2px;background:var(--blue);margin:10px auto 0}
.about{flex:none;margin-top:70px}
.about-body{width:1010px;margin:30px auto 0;font-size:12.5px;line-height:1.7;color:var(--muted)}
.about-body p{margin-bottom:18px}
.featured{flex:none;margin-top:26px}
.cards{display:flex;gap:24px;justify-content:center;margin-top:40px}
.card{width:234px;height:170px;border:1px solid var(--line);padding:6px;background:#fff}
.card-photo{width:100%;height:100%}
.c1{background:linear-gradient(135deg,#c98b4f,#f0e2cf)}
.c2{background:linear-gradient(135deg,#dbe6ee,#8fb0c8)}
.c3{background:linear-gradient(135deg,#eeeeee,#b9bcc0)}
.c4{background:linear-gradient(135deg,#e9f1f5,#c7d8c2)}
.map{flex:1 1 auto;position:relative;margin-top:50px;min-height:260px;background:linear-gradient(180deg,var(--map),#dfe4e7);display:flex;align-items:center;justify-content:center}
.footer{flex:none;height:122px;background:var(--blue);color:#fff;text-align:center;padding-top:40px}
.footer-nav{display:flex;gap:26px;justify-content:center;font-size:11px;font-weight:600;text-transform:uppercase}
.footer small{display:block;margin-top:12px;font-size:10px;opacity:.9}
</style>
</head>
<body>
<div class="topbar"><span>Call 01 555 0192</span><span>Email info@meadowbank.example</span></div>

<header class="header">
  <div class="brand"><span class="brand-dot"></span>Meadowbank Pharmacy</div>
  <nav class="nav">
    <a class="active" href="#">Home</a><a href="#">About Us</a><a href="#">Locations</a><a href="#">Timings</a><a href="#">Contact</a>
  </nav>
</header>

<section class="hero">
  <div class="hero-photo" role="img" aria-label="Close-up of white and green capsules and tablets on a light surface"></div>
  <div class="arrow left"><svg width="12" height="12" viewBox="0 0 12 12"><path d="M8 1 3 6l5 5" fill="none" stroke="#555" stroke-width="2"/></svg></div>
  <div class="arrow right"><svg width="12" height="12" viewBox="0 0 12 12"><path d="M4 1l5 5-5 5" fill="none" stroke="#555" stroke-width="2"/></svg></div>
  <div class="hero-copy">
    <h1 class="hero-title">Welcome to Meadowbank Pharmacy</h1>
    <p class="hero-text">We prepare medicines made to measure for each patient, in our purpose built laboratory, with care and precision.</p>
    <a class="btn" href="#">Read more</a>
  </div>
</section>

<section class="features">
  <div class="feature green">
    <svg width="46" height="46" viewBox="0 0 46 46"><path d="M17 6h12M19 6v13L9 38a3 3 0 0 0 3 4h22a3 3 0 0 0 3-4L27 19V6" fill="none" stroke="#fff" stroke-width="2.5"/></svg>
    <h3>We do Compounding</h3>
    <p>Tailored preparations for people and animals, made fresh in our own lab.</p>
  </div>
  <div class="feature blue">
    <svg width="46" height="46" viewBox="0 0 46 46"><path d="M23 42S10 27 10 18a13 13 0 0 1 26 0c0 9-13 24-13 24z" fill="none" stroke="#fff" stroke-width="2.5"/><circle cx="23" cy="18" r="5" fill="#fff"/></svg>
    <h3>Where we are</h3>
    <p>Visit our store on the high street, with easy parking close by.</p>
  </div>
  <div class="feature orange">
    <svg width="46" height="46" viewBox="0 0 46 46"><circle cx="23" cy="23" r="17" fill="none" stroke="#fff" stroke-width="2.5"/><path d="M23 13v11l7 5" fill="none" stroke="#fff" stroke-width="2.5"/></svg>
    <h3>When we are there</h3>
    <p>Open six days a week, with a pharmacist always on hand.</p>
  </div>
</section>

<section class="about">
  <h2 class="section-title">About Meadowbank Pharmacy</h2>
  <div class="about-body">
    <p>Historically, compounding was the heart of every pharmacy. Before mass production, pharmacists prepared each remedy by hand to suit the person in front of them, weighing, mixing and labelling every dose themselves.</p>
    <p>That tradition fell away as factory made medicines became the norm, yet many patients still need doses, forms and strengths that are not sold off the shelf.</p>
    <p>We are not replacing licensed products. We fill the gaps they leave, for allergies, swallowing problems, unusual doses and discontinued lines.</p>
    <p>Meadowbank Pharmacy brings modern equipment and careful technique together, so that a prescriber's exact instructions can be followed for every preparation we make, whether a cream, a capsule, a liquid or a flavoured medicine for a pet.</p>
    <p>As a dedicated team, we keep learning, checking our methods against current standards and working closely with doctors, dentists and veterinary surgeons.</p>
    <p>Our laboratory was designed for the task, with clean work areas, calibrated balances and documented procedures that support safe, consistent results.</p>
    <p>Every preparation is checked by a registered pharmacist before it leaves us, and each label carries clear directions and a use by date.</p>
    <p>Our aim as a community pharmacy is to offer a friendly, personal service. Ask us about your needs, in store or by phone, and we will gladly help.</p>
  </div>
</section>

<section class="featured">
  <h2 class="section-title">Featured products &amp; services</h2>
  <div class="cards">
    <div class="card"><div class="card-photo c1" role="img" aria-label="Amber medicine bottles on a shelf"></div></div>
    <div class="card"><div class="card-photo c2" role="img" aria-label="Pharmacist preparing a medicine in the laboratory"></div></div>
    <div class="card"><div class="card-photo c3" role="img" aria-label="Blister packs of tablets"></div></div>
    <div class="card"><div class="card-photo c4" role="img" aria-label="Assorted capsules and creams"></div></div>
  </div>
</section>

<section class="map" role="img" aria-label="Street map showing the pharmacy location">
  <svg width="30" height="42" viewBox="0 0 30 42"><path d="M15 41S2 24 2 15a13 13 0 0 1 26 0c0 9-13 26-13 26z" fill="#2e8fd6"/><circle cx="15" cy="15" r="5" fill="#fff"/></svg>
</section>

<footer class="footer">
  <nav class="footer-nav"><span>Home</span><span>About Us</span><span>Locations</span><span>Timings</span><span>Contact</span></nav>
  <small>© 2024 Meadowbank Pharmacy</small>
</footer>
</body>
</html>
```